I need a logo design for a new company based in Tucson called "Mindtrail Lee Corwin". I am a psychotherapist that specializes in clinical psychology with athletes and performers. The final design should incorporate the psychology symbol as a watermark. The logo should convey movement and fluidity. "Mindtrail" is a bit of a play on words combining psychology (head) with sports (coach). Other design interests include mid-century, Harold Ames Whitby. I will want to use the logo for business cards, letterhead and marketing brochures. I will put together a website at a later date. I am attaching a file with some pertinent information for the business card. Thank you.
Lee Corwin
mindtrailleecorwin@quillpost.net

Thank you all for the submissions so far.  I have submitted an additional file with a draft of a new design idea.  Since "mindtrail" is a bit of a play on words, I would like to see something with the two "H's" look something like quotation marks.  If the psychology logo is to be included at all, it needs to be less prominent.     Thank you all.  Lee                               

Target Market(s)

1) Adolescent and adult athletes and performers who are looking to increase their level of performance (Sport and Performance Psychology)
2) Adult psychotherapy patients (Clinical psychology)

Industry/Entity Type

Marketing

Colors

Designer to choose colors to be used in the design.

Requirements
Must have
• 1) Since "mindtrail" is a bit of a play on words, The "H's" need to be in a font that looks somewhat like quotation marks.

Nice to have
• Logo on one side. All other info on the backside?

```html
<!DOCTYPE html>
<html lang="en">
<head>
<meta charset="utf-8">
<title>Mindtrail – Business Card</title>
<link rel="stylesheet" href="https://fonts.googleapis.com/css2?family=Alegreya:ital,wght@1,500&family=Lato:wght@400;700;900&display=swap">
<style>
  :root {
    --backdrop: #d9d9d9;
    --card: #3b3939;
    --mint: #a9dcc2;
    --mint-soft: #9fd2b8;
    --shadow: rgba(0, 0, 0, 0.28);
  }
  * { margin: 0; padding: 0; box-sizing: border-box; }
  html, body {
    width: 1200px;
    height: 1000px;
    overflow: hidden;
    background: var(--backdrop);
  }
  .canvas {
    position: relative;
    width: 1200px;
    height: 1000px;
  }
  .card {
    position: absolute;
    left: 250px;
    width: 700px;
    height: 400px;
    background: var(--card);
    border-radius: 22px;
    box-shadow: 0 10px 24px var(--shadow);
    color: var(--mint);
    font-family: "Lato", sans-serif;
  }
  .card--front { top: 60px; }
  .card--back { top: 540px; }

  .brand {
    position: absolute;
    left: 0;
    right: 0;
    top: 108px;
    text-align: center;
  }
  .brand__row {
    display: inline-flex;
    align-items: center;
    gap: 18px;
  }
  .brand__square {
    width: 26px;
    height: 26px;
    background: var(--mint);
  }
  .brand__name {
    font-family: "Lato", sans-serif;
    font-weight: 900;
    font-size: 96px;
    line-height: 1;
    letter-spacing: 2px;
    color: var(--mint);
  }
  .brand__tagline {
    margin-top: 26px;
    font-weight: 700;
    font-size: 22px;
    letter-spacing: 3.5px;
    text-transform: uppercase;
    color: var(--mint);
  }

  .holder {
    position: absolute;
    left: 0;
    right: 0;
    top: 46px;
    text-align: center;
  }
  .holder__name {
    font-family: "Alegreya", serif;
    font-style: italic;
    font-weight: 500;
    font-size: 46px;
    line-height: 1.1;
    color: var(--mint);
  }
  .holder__title {
    margin-top: 4px;
    font-weight: 700;
    font-size: 19px;
    color: var(--mint-soft);
  }
  .contact {
    position: absolute;
    left: 0;
    right: 0;
    top: 196px;
    list-style: none;
    text-align: center;
    font-size: 20px;
    line-height: 38px;
    color: var(--mint);
  }
  .contact__label { font-weight: 700; }
</style>
</head>
<body>
<main class="canvas">
  <section class="card card--front" aria-label="Card front">
    <div class="brand">
      <div class="brand__row">
        <span class="brand__square" aria-hidden="true"></span>
        <span class="brand__name">Mindtrail</span>
      </div>
      <p class="brand__tagline">Clinical &amp; Performance Psychology</p>
    </div>
  </section>

  <section class="card card--back" aria-label="Card back">
    <div class="holder">
      <h1 class="holder__name">Lee H. Corwin, MA, LLC</h1>
      <p class="holder__title">Licensed Professional Counselor</p>
    </div>
    <ul class="contact">
      <li><span class="contact__label">Fax:</span> 520.555.0147</li>
      <li><span class="contact__label">Mobile:</span> 520.555.0182</li>
      <li><span class="contact__label">Email:</span> mindtrailleecorwin@quillpost.net</li>
      <li><span class="contact__label">Address:</span> 4125 East Sable #210 Tucson,&nbsp; AZ 85716</li>
    </ul>
  </section>
</main>
</body>
</html>
```